Information One Page for Email

I am looking for a informative attachment I can send with an introductive email for Meridale Slab Works. Something I can also Mail.

Meridale Slab Works is the leader in Rebar Post Tension Cable Placement and Post Tension Cable repair. Outside of cable placement and repair we do concrete repair, Parking Garage restoration and
Updates

Content

Post Tension Repair and Concrete Restoration
Post-tensioning is a revolutionary method in concrete construction that enhances the strength and durability of structures. However, like all construction ele-ments, post-tension cables can experience wear and damage over time. Ensuring timely and effective repair is crucial for maintaining the safety and integrity of your building.
Why Post-Tension Cable Repair is Essential
1. **Structural Integrity**: Damaged or deteriorated cables can compromise the structural integrity of your building, leading to safety hazards and potential structural failures.
2. **Extended Lifespan**: Regular maintenance and repair of post-tension cables extend the lifespan of your structure, ensuring it remains safe and function-al for years to come.
3. **Cost-Effective**: Addressing cable issues early on prevents more severe damage and costly repairs down the line.
Common Signs of Post-Tension Cable Issues
- Cracks in concrete surfaces
- Unusual noises or popping sounds
- Visible cable ends or broken strands
- Water leakage through cracks
Our Repair Process
1. **Inspection and Assessment**: Our team conducts a thorough inspection to identify the extent of the damage and determine the appropriate repair meth-ods.
2. **Cable Repair or Replacement**: Depending on the severity, we either re-pair the existing cables or replace them with new ones to restore full functional-ity.
3. **Sealing and Protection**: After repairing, we seal the affected areas to protect against moisture and future damage.
4. **Quality Assurance**: We perform rigorous quality checks to ensure the repairs meet industry standards and the structure is safe for use.
Why Choose Us
- **Expertise and Experience**: With years of experience in post-tension cable repair, our team is skilled in handling even the most complex repairs efficiently and effectively.
- **Advanced Technology**: We use the latest technology and materials to ensure durable and long-lasting repairs.
- **Customer Satisfaction**: Our commitment to quality and customer satisfaction sets us apart. We work closely with our clients to ensure their needs are met and expectations exceeded.
Contact Us
If you suspect issues with your post-tension cables or need a routine inspection, don't hesitate to contact us. Our experts are ready to provide the best solutions to keep your structures safe and secure.
Ensure the safety and longevity of your building with our professional post-tension cable repair services. Trust us to deliver quality and reliability every time.

```html
<!DOCTYPE html>
<html lang="en">
<head>
<meta charset="utf-8">
<title>Meridale Slab Works – Post Tension Repair and Concrete Restoration</title>
<link rel="stylesheet" href="https://fonts.googleapis.com/css2?family=Inter+Tight:wght@400;500;600;700&display=swap">
<style>
  :root{
    --paper:#faf3ef;
    --forest:#066a37;
    --mint:#1ee47f;
    --ink:#2b2b2b;
    --body:#3d3d3d;
    --alert:#e0201b;
    --rule:#6b6b6b;
    --frame:#2f8a58;
  }
  *{margin:0;padding:0;box-sizing:border-box}
  html,body{width:924px;height:1200px;overflow:hidden;background:var(--paper)}
  body{font-family:"Inter Tight",Arial,sans-serif;color:var(--body);position:relative;letter-spacing:-0.02em}
  .abs{position:absolute}

  .hero{left:30px;top:30px;width:419px;height:342px;background:var(--forest);border-radius:10px;padding:28px 26px}
  .hero-title{font-weight:700;font-size:40px;line-height:46px;color:#fff;letter-spacing:-0.03em}
  .hero-title .accent{color:var(--mint)}
  .hero-lead{margin-top:14px;color:#fff;font-size:19.5px;line-height:24px;width:360px}

  .intro{left:30px;top:404px;width:400px;font-size:19.5px;line-height:24px}
  .intro strong{font-weight:500;color:var(--ink)}

  .why-title{left:30px;top:552px;font-size:26px;line-height:33px;font-weight:700;color:var(--ink)}
  .why-title .accent,.signs-title .accent{color:var(--forest)}
  .benefit h3{font-size:16px;font-weight:600;color:var(--ink);display:flex;align-items:center;gap:10px;margin-bottom:8px}
  .benefit p{font-size:15.5px;line-height:20px}
  .b-structure{left:225px;top:556px;width:208px}
  .b-lifespan{left:30px;top:708px;width:190px}
  .b-cost{left:250px;top:724px;width:170px}
  .b-lifespan h3{position:relative}
  .b-lifespan .icon{position:absolute;left:150px;top:-30px}
  .line{background:var(--rule)}

  .signs-title{left:30px;top:892px;font-size:26px;line-height:33px;font-weight:700;color:var(--ink)}
  .signs-title .warn{color:var(--alert)}
  .signs{left:55px;top:964px;list-style:none;font-size:16.5px;line-height:24.5px}

  .brand{left:500px;top:70px;width:380px;display:flex;align-items:center;gap:12px}
  .brand-mark{width:22px;height:22px;background:var(--forest)}
  .brand-name{font-size:30px;font-weight:700;color:var(--forest);letter-spacing:-0.02em}

  .process{left:510px;top:182px;width:384px;height:578px;border:1px solid #b9cfc1;border-radius:8px;background:var(--paper)}
  .process h2{position:absolute;left:22px;top:20px;font-size:30px;font-weight:700;color:var(--forest);letter-spacing:-0.03em}
  .step h3{font-size:16.5px;font-weight:600;color:var(--ink);margin-bottom:8px}
  .step p{font-size:16.5px;line-height:21px}
  .s1{left:533px;top:262px;width:250px}
  .s2{left:630px;top:389px;width:240px}
  .s3{left:533px;top:515px;width:245px}
  .s4{left:626px;top:634px;width:230px}
  .art{border-radius:4px}
  .art-inspect{left:800px;top:247px;width:90px;height:127px;background:linear-gradient(160deg,#8fdc4e,#2f3b3a)}
  .art-cable{left:510px;top:380px;width:108px;height:110px;background:linear-gradient(160deg,#4b5ea8,#e6e9f3)}
  .art-seal{left:804px;top:500px;width:86px;height:100px;background:linear-gradient(160deg,#9be6b0,#e46a2c)}
  .art-qa{left:486px;top:632px;width:128px;height:84px;background:linear-gradient(160deg,#a6e8c6,#e9faf1)}

  .choose-label{left:470px;top:1029px;transform-origin:0 0;transform:rotate(-90deg);font-size:27px;font-weight:700;color:var(--ink);white-space:nowrap;width:220px;letter-spacing:-0.02em}
  .choose-label .accent{color:var(--forest)}
  .reasons{left:535px;top:780px;width:360px}
  .reason{margin-bottom:10px}
  .reason h3{font-size:17px;font-weight:500;color:var(--ink);display:flex;align-items:center;gap:10px;margin-bottom:3px}
  .reason p{font-size:16px;line-height:21px;color:var(--body)}

  .contact{left:30px;top:1079px;width:864px;height:106px;border:1px solid #9fc3ad;border-radius:8px;text-align:center;padding:12px 24px 0}
  .contact p{font-size:12.6px;line-height:17px;color:var(--body)}
  .contact .url{margin-top:8px;font-size:17px;color:var(--forest);display:inline-flex;align-items:center;gap:12px}
</style>
</head>
<body>

<section class="hero abs">
  <h1 class="hero-title">POST TENSION<br>REPAIR <span class="accent">AND<br>CONCRETE<br>RESTORATION</span></h1>
  <p class="hero-lead">Post-tensioning is a revolutionary method in concrete construction that enhances the strength and durability of structures.</p>
</section>

<p class="intro abs">However, like all construction elements, post-tension cables can experience wear and damage over time. Ensuring <strong>timely</strong> and <strong>effective repair</strong> is crucial for maintaining the safety and integrity of your building.</p>

<h2 class="why-title abs">Why <span class="accent">Post<br>Tension<br>Cable Repair</span><br>is Essential</h2>

<div class="line abs" style="left:227px;top:530px;width:222px;height:1px"></div>
<div class="line abs" style="left:437px;top:524px;width:1px;height:176px"></div>
<div class="line abs" style="left:220px;top:695px;width:226px;height:1px"></div>
<div class="line abs" style="left:226px;top:687px;width:1px;height:176px"></div>
<div class="line abs" style="left:42px;top:856px;width:190px;height:1px"></div>

<div class="benefit b-structure abs">
  <h3>Structural Integrity
    <svg width="22" height="22" viewBox="0 0 22 22" fill="none" stroke="#066a37" stroke-width="2"><path d="M3 2v19M19 2v19M3 6h16M3 11h16M3 16h16M8 2v19M14 2v19"/></svg>
  </h3>
  <p>Damaged or deteriorated cables can compromise the structural integrity of your building, leading to safety hazards &amp; structural failures.</p>
</div>

<div class="benefit b-lifespan abs">
  <h3>Extended Lifespan
    <svg class="icon" width="28" height="28" viewBox="0 0 28 28"><rect x="3" y="2" width="8" height="20" fill="#066a37"/><rect x="1" y="22" width="14" height="3" fill="#066a37"/><circle cx="20" cy="19" r="7" fill="#066a37"/><path d="M20 15v4l3 2" stroke="#fff" stroke-width="1.6" fill="none"/></svg>
  </h3>
  <p>Maintenance and repair of post-tension cables extend the lifespan of your structure, ensuring it remains safe &amp; functional for years to come.</p>
</div>

<div class="benefit b-cost abs">
  <h3>Cost-Effective
    <svg width="26" height="26" viewBox="0 0 26 26"><circle cx="16" cy="7" r="6" fill="#066a37"/><text x="16" y="10.5" font-size="9" text-anchor="middle" fill="#fff" font-family="Arial">$</text><path d="M2 19l6-4h6l-3 3h5l7-4" stroke="#066a37" stroke-width="2.4" fill="none" stroke-linecap="round"/></svg>
  </h3>
  <p>Addressing cable issues early on prevents more severe damage and costly repairs down the line.</p>
</div>

<h2 class="signs-title abs"><span class="accent">Common Signs</span> of Post-Tension<br>Cable <span class="warn">Issues</span></h2>
<ul class="signs abs">
  <li>Cracks in concrete surfaces</li>
  <li>Unusual noises or popping sounds</li>
  <li>Visible cable ends or broken strands</li>
  <li>Water leakage through cracks</li>
</ul>

<div class="brand abs">
  <span class="brand-mark"></span>
  <span class="brand-name">Meridale Slab Works Inc.</span>
</div>

<section class="process abs">
  <h2>Our Repair Process</h2>
</section>
<div class="art art-inspect abs" role="img" aria-label="Illustration of two inspectors in green uniforms reviewing a clipboard and plans"></div>
<div class="step s1 abs">
  <h3>Inspection &amp; Assessment</h3>
  <p>Our team conducts a thorough inspection to identify the extent of the damage and determine the appropriate repair meth-ods.</p>
</div>
<div class="art art-cable abs" role="img" aria-label="Illustration of a technician kneeling to repair a cable beside a toolbox"></div>
<div class="step s2 abs">
  <h3>Cable Repair or Replacement</h3>
  <p>Depending on severity, we either repair existing cables or replace them with new ones to restore full functionality.</p>
</div>
<div class="art art-seal abs" role="img" aria-label="Illustration of a worker in a hard hat beside a green office tower"></div>
<div class="step s3 abs">
  <h3>Sealing and Protection</h3>
  <p>After repairing, we seal the affected areas to protect against moisture &amp; future damage.</p>
</div>
<div class="art art-qa abs" role="img" aria-label="Illustration of an inspector approving a checklist in front of buildings and a crane"></div>
<div class="step s4 abs">
  <h3>Quality Assurance</h3>
  <p>We perform rigorous quality checks to ensure the repairs meet industry standards and the structure is safe for use.</p>
</div>

<h2 class="choose-label abs"><span class="accent">Why Choose</span> Us</h2>

<div class="reasons abs">
  <div class="reason">
    <h3><svg width="14" height="12" viewBox="0 0 14 12"><path d="M1 6l4 4 8-9" stroke="#111" stroke-width="2.2" fill="none"/></svg>Expertise and Experience</h3>
    <p>Years of experience in post-tension cable repair, our team is skilled in handling the most complex repairs efficiently &amp; effectively.</p>
  </div>
  <div class="reason">
    <h3><svg width="14" height="12" viewBox="0 0 14 12"><path d="M1 6l4 4 8-9" stroke="#111" stroke-width="2.2" fill="none"/></svg>Advanced Technology</h3>
    <p>We use the latest technology and materials to ensure durable and long-lasting repairs.</p>
  </div>
  <div class="reason">
    <h3><svg width="14" height="12" viewBox="0 0 14 12"><path d="M1 6l4 4 8-9" stroke="#111" stroke-width="2.2" fill="none"/></svg>Customer Satisfaction</h3>
    <p>Our commitment to quality and customer satisfaction sets us apart. We work closely with our clients to ensure their needs are met and expectations exceeded.</p>
  </div>
</div>

<footer class="contact abs">
  <p>If you suspect issues with your post-tension cables or need a routine inspection, don't hesitate to contact us. Our experts are ready to provide the best solutions to keep your structures safe &amp; secure. Ensure the safety and longevity of your building with our professional post-tension cable repair services. Trust us to deliver quality and reliability every time.</p>
  <span class="url">
    <svg width="10" height="13" viewBox="0 0 10 13"><path d="M1 1l8 6-4 .6 2 4.4-1.6.7-2-4.4L1 11z" fill="#066a37"/></svg>
    meridaleslabworks.com
  </span>
</footer>

</body>
</html>
```